Human Resource Consulting practice needs a business card design

We need a business card design (double sided colour) for our Human Resource (HR) consulting practice in regional New South Wales, australia. Our business name is Staff Compass. We support small and medium business across the Mid North Coast of New South Wales by providing them with outsourced HR support, services and products to help them achieve compliance with workplace legislation and across all areas of the employment lifecycle from recruitment to termination and everything in between. Our corporate colours are hot pink and black. The final design should communicate professionalism, trust, people focus.
I have attached the current (old) business card for your reference.

Target Market(s)

Business owners and high level managers

Industry/Entity Type

Business

Contact Information for Business Card

Name
Title
Phone no
Mobile no
Address
PO Box
email address
website

Colors
e34197

Requirements
Must have
• Tempate for changing business card personal details including Name, position title, mobile number, email address.
• Keep current logo and colours as per attached
• Logo must be presented in 2 colours or black only not white
Nice to have
• One side logo and graphic only other side logo and personal details
Should not have
• Should not be the same as the current version (attached) but a modern interpretation.
• Does not need a busy reverse side with our list of services as per current version. I feel this is too busy.
• No photos

```html
<!DOCTYPE html>
<html lang="en">
<head>
<meta charset="utf-8">
<title>Staff Compass – Business Card</title>
<link rel="stylesheet" href="https://fonts.googleapis.com/css2?family=Tinos:wght@400;700&display=swap">
<style>
  :root {
    --pink: #d6007a;
    --pink-deep: #c4006f;
    --ink: #1c1c1c;
    --black: #050505;
    --paper-light: #ffffff;
    --paper-grey: #cfcfcf;
    --contact-text: #dcdcdc;
    --name-text: #f1f1f1;
    --stage: #1b1b1b;
  }
  * { margin: 0; padding: 0; box-sizing: border-box; }
  html, body {
    width: 1189px; height: 1200px; overflow: hidden;
    background: var(--stage);
    font-family: "Tinos", "Times New Roman", serif;
  }
  .canvas { position: relative; width: 1189px; height: 1200px; }

  .card {
    position: absolute; left: 140px; width: 917px; height: 524px; overflow: hidden;
  }

  /* Reverse side: tagline and name only */
  .card--reverse {
    top: 45px;
    background: radial-gradient(ellipse at 55% 100%, var(--paper-light) 0%, #ececec 45%, var(--paper-grey) 100%);
    color: var(--ink);
  }
  .reverse__tagline {
    position: absolute; left: 103px; top: 84px;
    font-weight: 700; font-size: 24px; line-height: 31px;
  }
  .brand--vertical {
    position: absolute; left: 700px; top: 50px; height: 420px; width: 100px;
    display: flex; align-items: center; justify-content: center;
  }
  .brand--vertical .brand__name {
    writing-mode: vertical-rl; transform: rotate(180deg);
    font-size: 70px; font-weight: 700; color: var(--pink); white-space: nowrap;
    display: flex; align-items: center; gap: 14px; line-height: 1;
  }
  .brand__dot { width: 12px; height: 12px; background: var(--pink); display: inline-block; flex: none; }

  /* Contact side */
  .card--contact { top: 623px; background: var(--black); }
  .card__art { position: absolute; inset: 0; }
  .brand--horizontal {
    position: absolute; left: 60px; top: 276px;
    font-size: 48px; line-height: 1; font-weight: 700; color: var(--pink);
    display: flex; align-items: baseline; gap: 8px; white-space: nowrap;
  }
  .person {
    position: absolute; right: 59px; top: 76px; text-align: right;
  }
  .person__name { font-size: 48px; font-weight: 700; color: var(--name-text); line-height: 50px; }
  .person__title { font-size: 17px; color: var(--name-text); margin-top: 2px; letter-spacing: 0.2px; }
  .person__address { font-size: 20px; line-height: 25px; color: var(--name-text); margin-top: 50px; }
  .contacts {
    position: absolute; right: 59px; top: 336px; list-style: none;
    font-size: 20px; line-height: 24px; color: var(--contact-text);
  }
  .contacts li { display: flex; justify-content: flex-end; align-items: center; gap: 12px; }
  .contacts svg { width: 16px; height: 16px; flex: none; }
</style>
</head>
<body>
<div class="canvas">

  <section class="card card--reverse" aria-label="Card back – tagline and name">
    <h2 class="reverse__tagline">Building Exciting, Engaging<br>&amp; Productive Workplaces</h2>
    <div class="brand brand--vertical">
      <span class="brand__name">Staff Compass<span class="brand__dot"></span></span>
    </div>
  </section>

  <section class="card card--contact" aria-label="Card front – contact details">
    <svg class="card__art" viewBox="0 0 917 524" width="917" height="524" aria-hidden="true">
      <defs>
        <linearGradient id="band" x1="0" y1="0" x2="1" y2="1">
          <stop offset="0" stop-color="#d6007a"/>
          <stop offset="1" stop-color="#c4006f"/>
        </linearGradient>
        <radialGradient id="disc" cx="0.55" cy="0.3" r="0.8">
          <stop offset="0" stop-color="#fafafa"/>
          <stop offset="1" stop-color="#cfcfcf"/>
        </radialGradient>
        <linearGradient id="rim" x1="0" y1="0" x2="1" y2="0">
          <stop offset="0.6" stop-color="#9a9a9a"/>
          <stop offset="1" stop-color="#3a3a3a"/>
        </linearGradient>
      </defs>
      <rect x="0" y="0" width="917" height="275" fill="url(#band)"/>
      <rect x="0" y="275" width="917" height="249" fill="#050505"/>
      <circle cx="170" cy="261" r="290" fill="url(#rim)"/>
      <circle cx="164" cy="261" r="280" fill="#e6e6e6"/>
      <circle cx="160" cy="261" r="270" fill="url(#disc)"/>
    </svg>

    <div class="brand brand--horizontal">Staff Compass<span class="brand__dot"></span></div>

    <div class="person">
      <p class="person__name">Maren Holt</p>
      <p class="person__title">PRINCIPAL CONSULTANT</p>
      <p class="person__address">PO Box 318, Harbour Bend,<br>NSW 2450</p>
    </div>

    <ul class="contacts">
      <li>02 5550 1842
        <svg viewBox="0 0 16 16" aria-label="Phone"><path d="M2 6c0-2 2-3 6-3s6 1 6 3l-3 1-1-2H6L5 7 2 6z M4 8h8l1 5H3z" fill="var(--pink)"/></svg>
      </li>
      <li>0400 555 213
        <svg viewBox="0 0 16 16" aria-label="Mobile"><rect x="4.5" y="1.5" width="7" height="13" rx="1.5" fill="none" stroke="var(--pink)" stroke-width="1.5"/><circle cx="8" cy="12" r="0.9" fill="var(--pink)"/></svg>
      </li>
      <li>02 5550 1877
        <svg viewBox="0 0 16 16" aria-label="Fax"><rect x="4" y="1" width="8" height="4" fill="var(--pink)"/><rect x="1" y="5" width="14" height="6" rx="1" fill="var(--pink)"/><rect x="4" y="10" width="8" height="5" fill="var(--pink)" stroke="var(--black)" stroke-width="1"/></svg>
      </li>
      <li>www.staffcompass.com.au
        <svg viewBox="0 0 16 16" aria-label="Website"><rect x="1.5" y="2" width="13" height="9" fill="none" stroke="var(--pink)" stroke-width="1.5"/><rect x="7" y="11" width="2" height="2" fill="var(--pink)"/><rect x="4.5" y="13" width="7" height="1.5" fill="var(--pink)"/></svg>
      </li>
      <li>maren@staffcompass.com.au
        <svg viewBox="0 0 16 16" aria-label="Email"><rect x="1" y="3" width="14" height="10" fill="var(--pink)"/><path d="M1 3l7 6 7-6" fill="none" stroke="var(--black)" stroke-width="1.2"/></svg>
      </li>
    </ul>
  </section>

</div>
</body>
</html>
```